Business Card Design For A Cajun Seafood Restaurant

We are opening a cajun seafood restaurant in a week. We mainly serve cajun seafood which is orginally from Louisiana. We want design on both sides of a business card. I have menu on the website. You can go to www.reednkettle.example to check out our menu.

Restaurant name: Reed N' Kettle
Phone: +1 (555) 304-7712
Address: 48206 Ludlow Row, #7, Bexmoor Flats, Ca90000
Email: reednkettle@mailbox.example
Website: www.reednkettle.example

Maybe add social media icons (facebook, instagram) if looks nice on the business card.
facebook.com/reednkettle
instagram.com/reednkettle or @reednkettle

Attached is the logo and other business card samples that I like.

```html
<!DOCTYPE html>
<html lang="en">
<head>
<meta charset="utf-8">
<title>Reed N' Kettle – Business Card</title>
<link rel="stylesheet" href="https://fonts.googleapis.com/css2?family=Open+Sans:wght@400;600;700;800&display=swap">
<style>
  :root {
    --backdrop: #3a3a3a;
    --card: #ffffff;
    --orange: #f75f00;
    --gold: #f5c400;
    --ink: #111111;
    --text: #222222;
    --white: #ffffff;
  }
  * { box-sizing: border-box; margin: 0; padding: 0; }
  html, body {
    width: 1200px; height: 750px; overflow: hidden;
    background: var(--backdrop);
    font-family: "Open Sans", Arial, sans-serif;
  }
  .canvas { position: relative; width: 1200px; height: 750px; }
  .card {
    position: absolute; top: 228px;
    width: 460px; height: 262px;
    background: var(--card);
    border-radius: 10px;
    overflow: hidden;
  }
  .card--front { left: 124px; }
  .card--back { left: 618px; }

  .swoosh { position: absolute; inset: 0; width: 460px; height: 262px; }

  .holder { position: absolute; left: 26px; top: 20px; }
  .holder__name { color: var(--orange); font-size: 17px; font-weight: 600; letter-spacing: .2px; }
  .holder__role { color: var(--text); font-size: 13px; margin-top: -2px; }

  .brand {
    position: absolute;
    display: flex; align-items: center; gap: 8px;
    color: var(--ink); font-weight: 800; white-space: nowrap;
  }
  .brand__dot { border-radius: 50%; background: var(--orange); flex: none; }
  .card--front .brand { left: 90px; top: 120px; font-size: 22px; }
  .card--front .brand__dot { width: 16px; height: 16px; }
  .card--back .brand { left: 50%; top: 132px; transform: translateX(-50%); font-size: 30px; }
  .card--back .brand__dot { width: 20px; height: 20px; }

  .contacts {
    position: absolute; right: 16px; top: 174px;
    color: var(--white); font-size: 12.5px; text-align: right; line-height: 17.5px;
  }
  .contacts__row { display: flex; justify-content: flex-end; align-items: center; gap: 6px; }
  .contacts__row svg { width: 12px; height: 12px; flex: none; }
  .contacts__address { margin-top: 3px; }

  .social {
    position: absolute; left: 0; right: 0; top: 220px;
    display: flex; justify-content: center; align-items: center; gap: 4px;
    color: var(--text); font-size: 13px;
  }
  .social__mark { width: 17px; height: 17px; border-radius: 50%; background: var(--orange); flex: none; }
  .social__mark--square { border-radius: 4px; margin-left: 4px; }
</style>
</head>
<body>
<div class="canvas">

  <section class="card card--front">
    <svg class="swoosh" viewBox="0 0 460 262" aria-hidden="true">
      <path d="M0 222 C 190 228 350 170 460 16 L460 262 L0 262 Z" fill="var(--orange)"/>
      <path d="M22 219 C 200 222 355 160 452 12" fill="none" stroke="var(--gold)" stroke-width="3"/>
      <path d="M20 224 C 200 228 360 166 456 16" fill="none" stroke="var(--ink)" stroke-width="4"/>
    </svg>

    <div class="holder">
      <p class="holder__name">DANA WHITLOW</p>
      <p class="holder__role">CEO/Founder</p>
    </div>

    <div class="brand"><span class="brand__dot"></span>Reed N' Kettle</div>

    <div class="contacts">
      <p class="contacts__row">+1 (555) 304-7712
        <svg viewBox="0 0 24 24"><path fill="#fff" d="M6.6 10.8a15 15 0 0 0 6.6 6.6l2.2-2.2a1 1 0 0 1 1-.25 11.4 11.4 0 0 0 3.6.57 1 1 0 0 1 1 1V20a1 1 0 0 1-1 1A17 17 0 0 1 3 4a1 1 0 0 1 1-1h3.5a1 1 0 0 1 1 1c0 1.25.2 2.45.57 3.57a1 1 0 0 1-.25 1z"/></svg>
      </p>
      <p class="contacts__row">reednkettle@mailbox.example
        <svg viewBox="0 0 24 24"><rect x="2" y="5" width="20" height="14" rx="1" fill="#fff"/><path d="M3 6l9 7 9-7" fill="none" stroke="var(--orange)" stroke-width="1.6"/></svg>
      </p>
      <p class="contacts__row">www.reednkettle.example
        <svg viewBox="0 0 24 24"><circle cx="12" cy="12" r="10" fill="#fff"/><path d="M2 12h20M12 2c3 3 3 17 0 20M12 2c-3 3-3 17 0 20" fill="none" stroke="var(--orange)" stroke-width="1.4"/></svg>
      </p>
      <p class="contacts__address">48206 Ludlow Row, #7, Bexmoor Flats, Ca90000</p>
    </div>
  </section>

  <section class="card card--back">
    <div class="brand"><span class="brand__dot"></span>Reed N' Kettle</div>
    <div class="social">
      <span class="social__mark"></span><span>reednkettle</span>
      <span class="social__mark social__mark--square"></span><span>@reednkettle</span>
    </div>
  </section>

</div>
</body>
</html>
```